Visitenkarten und Briefpapier
Zielgruppe
Planung und Realisierung von individuellen und wertbeständigen Kamin- und Ofenlösungen, sowie Fliesen- und Baddesign.
Aufgabenstellung
Wir benötigen ein möglichst schlichtes Design für Visitenkarten, bzw. Briefpapier. Für die Visitenkarten gerne auch Vorschläge mit Prägung, Ausstanzung oder mit Heißfolie. Auch Klappkarten wären denkbar. Das Design soll "das gewisse Etwas haben" und nicht zu verspielt sein.
Die Visitenkarten sind für die Firma KORVA, das Logo von der Ausstellung "raumfunke" soll dezent mit eingebunden werden (bei dem Briefpapier z.B. in der Fußzeile". Die farbliche Gestaltung sollte sich an den Farben des Logos orientieren.
Schriftart für Texte: Century Gothic
Schriftfarbe: RAL 7016
Nur eine Idee: Ich könnte mir auch gut vorstellen, dass die Visitenkarte aus einer Zündholzverpackung (wenn dann aber eine besondere mit nur einem Zündholz oder einem besonders breiten) besteht: http://glimmvelo.de/produkte_briefchen.php

```html
<!DOCTYPE html>
<html lang="de">
<head>
<meta charset="utf-8">
<title>Korva Briefpapier</title>
<link href="https://fonts.googleapis.com/css2?family=Questrial&display=swap" rel="stylesheet">
<style>
  :root {
    --backdrop: #ececec;
    --paper: #f7f7f7;
    --ink: #383e42;
    --ink-soft: #8a8f93;
  }
  * { margin: 0; padding: 0; box-sizing: border-box; }
  html, body { width: 1200px; height: 795px; overflow: hidden; }
  body {
    background: var(--backdrop);
    font-family: "Questrial", "Century Gothic", sans-serif;
    color: var(--ink);
    position: relative;
  }
  .brand-name { color: var(--ink); font-weight: normal; line-height: 1; }

  .brand-mark {
    position: absolute; left: 930px; top: 62px; width: 220px; text-align: right;
  }
  .brand-mark .brand-name { font-size: 64px; letter-spacing: 1px; }

  .letterhead {
    position: absolute; left: 190px; top: 38px; width: 509px; height: 720px;
    background: var(--paper);
    box-shadow: 0 2px 10px rgba(0,0,0,.12);
  }
  .letterhead > * { position: absolute; }
  .lh-logo { left: 40px; top: 36px; }
  .lh-logo .brand-name { font-size: 26px; letter-spacing: .5px; }
  .rule-top { left: 150px; top: 60px; width: 320px; border-top: 1px solid var(--ink); }
  .rule-logo { left: 40px; top: 88px; width: 110px; border-top: 1px solid var(--ink); }
  .sender-address { right: 39px; top: 38px; font-size: 5.5px; line-height: 7px; color: var(--ink-soft); display: flex; gap: 5px; align-items: center; }
  .letter-date { right: 39px; top: 112px; font-size: 6.5px; color: var(--ink-soft); }
  .recipient { left: 40px; top: 140px; font-size: 6.5px; line-height: 9.5px; color: var(--ink-soft); font-style: normal; }
  .salutation { left: 92px; top: 205px; font-size: 7px; }
  .letter-body { left: 92px; top: 222px; width: 340px; font-size: 6.8px; line-height: 10.5px; }
  .letter-body p + p { margin-top: 10px; }
  .closing { right: 60px; top: 404px; font-size: 7px; color: var(--ink-soft); text-align: right; }
  .closing .signature { text-decoration: underline; margin-top: 3px; }
  .contact-list { right: 26px; top: 436px; font-size: 5.8px; line-height: 9px; color: var(--ink-soft); list-style: none; }
  .contact-list li { display: flex; justify-content: flex-end; align-items: center; gap: 4px; }
  .contact-list svg { width: 6px; height: 6px; fill: var(--ink); }
  .company-info { left: 92px; top: 600px; font-size: 5.3px; line-height: 7.4px; color: var(--ink-soft); }
  .company-info strong { color: var(--ink); font-weight: normal; }
  .company-info .group + .group { margin-top: 3px; }
  .web-address { right: 70px; top: 650px; font-size: 6.5px; font-weight: bold; }
</style>
</head>
<body>

<div class="brand-mark">
  <div class="brand-name">Korva</div>
</div>

<main class="letterhead">
  <div class="lh-logo">
    <div class="brand-name">Korva</div>
  </div>
  <div class="rule-top"></div>
  <div class="rule-logo"></div>

  <div class="sender-address">
    <svg width="6" height="8" viewBox="0 0 6 8" aria-hidden="true"><path d="M3 0a3 3 0 0 1 3 3c0 2-3 5-3 5S0 5 0 3a3 3 0 0 1 3-3z" fill="#383e42"/><circle cx="3" cy="3" r="1" fill="#f7f7f7"/></svg>
    <div>Am Talgrund 14<br>34519 Diemelsee</div>
  </div>

  <div class="letter-date">London September 27, 2045</div>

  <address class="recipient">
    Sr. Tomas Ribera Soler<br>
    Director Comercial,<br>
    VELMARO, S.L.<br>
    c/ Almendro 22 08190 Sant Cugat
  </address>

  <div class="salutation">Dear Costumer,</div>

  <div class="letter-body">
    <p>Lorem ipsum dolor sit amet, consectetur adipiscing elit. Nam urna dui, accumsan auctor gravida nec, tempus nec ante. Nam vitae mi et est feugiat interdum. Nam eget tortor ligula consectetur tristique risus. Vivamus quis libero vel odio dictum rhoncus. Donec non metus sed quam posuere vestibulum. Quisque feugiat, mi quis congue egestas, lectus dui rutrum odio, et dignissim justo lorem quis nunc. Duis euismod purus sit amet orci cursus congue. Nulla vitae fermentum ante. Integer interdum massa vitae nisi scelerisque eu vulputate leo malesuada. Nulla in purus eu augue aliquet tempor nec condimentum neque. Nullam sed nulla metus.</p>
    <p>Suspendisse a risus quis risus condimentum gravida a in lacus. Aenean vel ipsum venenatis velit lobortis ultricies a nec risus. In hac habitasse platea dictumst. Aenean gravida rutrum accumsan. Nulla accumsan ullamcorper mauris ac iaculis. Donec volutpat turpis ac porta tincidunt felis neque blandit augue eget pharetra tortor turpis quis metus. Etiam non risus ac est luctus ornare. Vivamus porta, velit quis pharetra pellentesque, urna nisi tempus quam, non eleifend nulla leo vel dui.</p>
    <p>Suspendisse a risus quis risus condimentum gravida a in lacus. Aenean vel ipsum venenatis velit lobortis ultricies a nec risus. In hac habitasse platea dictumst. Aenean gravida rutrum accumsan. Nulla accumsan ullamcorper mauris ac iaculis. Donec volutpat, turpis ac porta tincidunt, felis neque.</p>
  </div>

  <div class="closing">
    <div>Best Regards</div>
    <div class="signature">Korva</div>
  </div>

  <ul class="contact-list">
    <li>05632 / 41 73 90 <svg viewBox="0 0 10 10" aria-hidden="true"><path d="M2 0h2l1 3-1.5 1a6 6 0 0 0 2.5 2.5L7 5l3 1v2c0 1-1 2-2 2C4 10 0 6 0 2c0-1 1-2 2-2z"/></svg></li>
    <li>05632 / 41 73 98 <svg viewBox="0 0 10 10" aria-hidden="true"><rect x="2" y="0" width="6" height="3"/><rect x="0" y="3" width="10" height="5" rx="1"/><rect x="2" y="7" width="6" height="3"/></svg></li>
    <li>info@korva-ofenbau.de <svg viewBox="0 0 10 10" aria-hidden="true"><path d="M0 2h10v6H0z"/><path d="M0 2l5 3.5L10 2" fill="none" stroke="#f7f7f7" stroke-width="1"/></svg></li>
  </ul>

  <div class="company-info">
    <div class="group">
      <strong>Geschäftsführer: Lena Hofbauer</strong><br>
      Amtsgericht Diemelsee | HRB 555, USt.-ID-Nr.: DE 987654321<br>
      Steuernummer: 025 544 12345
    </div>
    <div class="group">
      <strong>Bankverbindung 1</strong><br>
      BIC: WALDDEF1DMS<br>
      IBAN: DE71 31852 0007 0000 0218 63
    </div>
    <div class="group">
      <strong>Bankverbindung 2</strong><br>
      BIC: WALDDEF1DMS<br>
      IBAN: DE71 31852 0007 0000 0218 63
    </div>
  </div>

  <div class="web-address">www.korva-ofenbau.de</div>
</main>

</body>
</html>
```